Measuring Card for Eyelash Extensions

I want this made for my brand and in a format that I can get printed on standard size business cards (3.5 x 2 inches). The measurement must be accurate to the end of the business card because this will be put up to the eye to measure the lash length.
This is being sent to lash extension artists so they can measure the natural lash before they begin applying eyelash extensions. I want it to look like the card I attached and it must be an accurate measurement.

Target Market(s)

Lash Extension Artists

Font styles to use
Sans Serif

Colors
ffffff

Requirements
Must have
• Must be accurate measurement on a 3.5 x 2 inch business card.
Nice to have
• To look very similar to the card in the photo I attached.

```html
<!DOCTYPE html>
<html lang="en">
<head>
<meta charset="utf-8">
<title>Lash Length Measuring Card</title>
<link href="https://fonts.googleapis.com/css2?family=Open+Sans:wght@400;600;700;800&display=swap" rel="stylesheet">
<style>
  :root {
    --backdrop: #2b2b2d;
    --card: #ffffff;
    --purple: #3a1078;
    --tan: #caa58e;
    --tan-text: #b8896c;
    --ink: #3b2d6e;
    --rule: #d9d6dc;
    --photo-a: #9a9aa0;
    --photo-b: #e4e4e6;
  }
  * { box-sizing: border-box; margin: 0; padding: 0; }
  html, body {
    width: 1200px; height: 797px; overflow: hidden;
    background: var(--backdrop);
    font-family: "Open Sans", Arial, sans-serif;
  }
  .card {
    position: absolute; left: 400px; top: 48px;
    width: 400px; height: 700px;
    background: var(--card);
    overflow: hidden;
  }
  .card-header {
    height: 40px; background: var(--purple);
    color: #fff; font-weight: 800; font-size: 17px;
    letter-spacing: 0.5px; line-height: 40px;
    padding-left: 22px; text-transform: uppercase;
  }
  .brand { padding: 24px 22px 0; }
  .brand-name {
    font-size: 38px; font-weight: 600; letter-spacing: 0;
    color: var(--ink); line-height: 1.1;
  }
  .brand-tagline {
    margin-top: 6px; font-size: 12px;
    color: var(--ink);
  }
  .section-band {
    margin-top: 22px; height: 36px; background: var(--tan);
    color: #f6ede6; font-weight: 700; font-size: 16px;
    line-height: 36px; padding-left: 22px; text-transform: uppercase;
    letter-spacing: 0.5px;
  }
  .rules-text {
    padding: 12px 22px 0; font-size: 15px; line-height: 1.35;
    color: var(--ink);
  }
  .example {
    position: absolute; top: 318px; left: 22px; right: 22px;
    display: flex; gap: 20px; align-items: flex-end;
  }
  .lash-photo {
    width: 190px; height: 130px; flex: none;
    border: 6px solid var(--purple);
    background: linear-gradient(160deg, var(--photo-b) 0%, var(--photo-a) 100%);
  }
  .example-text { font-size: 16px; line-height: 1.3; color: var(--ink); }
  .example-title { color: var(--tan-text); font-weight: 600; font-size: 17px; text-transform: uppercase; }
  .example-text strong { color: var(--purple); font-weight: 800; text-decoration: underline; }
  .divider {
    position: absolute; left: 0; right: 0; height: 0;
    border-top: 1px dotted var(--rule);
  }
  .ruler { position: absolute; left: 0; top: 560px; }
  .ruler-label { font-family: "Open Sans", Arial, sans-serif; font-size: 10px; fill: var(--tan-text); font-weight: 600; }
</style>
</head>
<body>
  <main class="card">
    <div class="card-header">Measure Lash Length</div>

    <div class="brand">
      <div class="brand-name">Norvelle Studio</div>
      <div class="brand-tagline">Tools for lash artists</div>
    </div>

    <div class="section-band">Safe Lengths</div>
    <p class="rules-text">Never use extensions that are longer than +3mm from natural lashes. Never go +1mm on the inners.</p>

    <div class="example">
      <div class="lash-photo" role="img" aria-label="Close-up photo of natural lashes held against a millimetre ruler"></div>
      <div class="example-text">
        <div class="example-title">Example</div>
        <div>Natural lash<br>= 9mm</div>
        <div>Use <strong>MAXIMUM</strong><br>= 12mm</div>
      </div>
    </div>

    <div class="divider" style="top:480px"></div>
    <div class="divider" style="top:535px"></div>
    <div class="divider" style="top:655px"></div>

    <!-- 200px per inch: 1 mm = 7.874px, zero at the card edge -->
    <svg class="ruler" width="200" height="70" viewBox="0 0 200 70" aria-label="Millimetre ruler 0 to 20 mm">
      <g stroke="var(--purple)" stroke-width="1">
        <line x1="0" y1="0.5" x2="157.48" y2="0.5"/>
        <line x1="0.5" y1="0" x2="0.5" y2="18"/>
        <line x1="7.874" y1="0" x2="7.874" y2="8"/>
        <line x1="15.748" y1="0" x2="15.748" y2="8"/>
        <line x1="23.622" y1="0" x2="23.622" y2="8"/>
        <line x1="31.496" y1="0" x2="31.496" y2="8"/>
        <line x1="39.37" y1="0" x2="39.37" y2="18"/>
        <line x1="47.244" y1="0" x2="47.244" y2="8"/>
        <line x1="55.118" y1="0" x2="55.118" y2="8"/>
        <line x1="62.992" y1="0" x2="62.992" y2="8"/>
        <line x1="70.866" y1="0" x2="70.866" y2="8"/>
        <line x1="78.74" y1="0" x2="78.74" y2="18"/>
        <line x1="86.614" y1="0" x2="86.614" y2="8"/>
        <line x1="94.488" y1="0" x2="94.488" y2="8"/>
        <line x1="102.362" y1="0" x2="102.362" y2="8"/>
        <line x1="110.236" y1="0" x2="110.236" y2="8"/>
        <line x1="118.11" y1="0" x2="118.11" y2="18"/>
        <line x1="125.984" y1="0" x2="125.984" y2="8"/>
        <line x1="133.858" y1="0" x2="133.858" y2="8"/>
        <line x1="141.732" y1="0" x2="141.732" y2="8"/>
        <line x1="149.606" y1="0" x2="149.606" y2="8"/>
        <line x1="157.48" y1="0" x2="157.48" y2="18"/>
      </g>
      <text class="ruler-label" transform="translate(42.9 22) rotate(90)">05 mm</text>
      <text class="ruler-label" transform="translate(82.3 22) rotate(90)">10 mm</text>
      <text class="ruler-label" transform="translate(121.6 22) rotate(90)">15 mm</text>
      <text class="ruler-label" transform="translate(161 22) rotate(90)">20 mm</text>
    </svg>
  </main>
</body>
</html>
```